IT consulting company looking for a modern business design for a website and a new logo

We are the IT-consulting company VelmaTrix from Germany and need a new and modern business website and a new logo. We are specialized in output management. Our services include business analysis, outsourcing, development, training and project leading. We wish for a design with nature pictures (mountains, lakes, rivers, forests, etc.) for our company with the colors green and blue. If it is possible, a slow-mo video of a nature scene. The design should be responsive and the menu should change to a hamburger menu. The following are: • Services / Solutions 1. Output Management 2. Outsourcing 3. Development 4. Business Analyst 5. Training • Partners • Careers • About Us 1. Project A 2. Project B 3. Project C • Contact Notes for the following categories: For "Services / Solutions" we want to conclude some contents from all the sub-points and sub-points below. Additionally, we would like to see some sub-point under "Services / Solutions". For Output Management: "5 Benefits of Output Management Systems (OMS) - OMS Simplifies and Accelerates External Communication - Helps Reduce Communication Mistakes - Provides Customers With Fast and Secure Responses to your questions - Employees can focus on the essential as they can access prepared templates - Companies get complete transparency about their communication "The point" partner does not have sub-points. The content here is a quote and the logo from the company Brel. For now, just placeholders on this site. The next point wants to be "career" without sub-point and wants to contain some text. Carrer options wants to be listed here. Next point wants to be "About us", where we need sub-points which we do not know exactly at this moment, but they will contain text. By clicking directly on "About us" we want to include pictures and texts about 6 employees for which we only need placeholders at the moment. The last point wants to be "contact", where customers can send us messages. The main page should include a story about our company, which can be a placeholder for now. For reference, designs have a look at: https://brelvanto.de/ https://www.tarnopix.com/ https://www.pldrive.de/ We prefer WordPress designs, created with the plugin ELEMENTOR, so that we can easily edit the content by ourselves. The final design should look professional, competent and modern.

Target Market(s)

With our website, we want to reach the following target groups. <br> <br> <br> <br> <br> <br> <br> <br> <br> <br> <br> <br> <br> <br> <br> <br> <br> <br> <br> <br> <br> <br> <br> <br> <br> <br> <br> <br> <br> <br> <br> <br> <br> <br> <br> <br> <br> <br> <br> <br> <br> <br> <br> <br> <br> <br> <br> <br> <br>

Industry/Entity Type

Consulting

Logo Text

(optionally) VelmaTrix

Font styles to use
Sans Serif

Colors

Designer to choose colors to be used in the design.

Requirements
Must have
• 1. Outsourcing 3. Development 4. Business Analyst 5. Training • Partners • Careers • About Us 1. Project A 2. Project B 3. Project C • Contact The above-mentioned background picture with nature motifs (mountains, lakes, rivers, forests, etc.). WordPress design in primary colors blue and green.
Nice to have
• ELEMENTOR template. Effects for the background pictures. Counter of all successful projects for Output Management, Business Analyst and Training

```html
<!DOCTYPE html>
<html lang="en">
<head>
<meta charset="utf-8">
<title>VelmaTrix – Website Design Variants</title>
<link rel="stylesheet" href="https://fonts.googleapis.com/css2?family=Merienda:wght@400;700&family=PT+Sans:wght@400;700&display=swap">
<style>
  :root{
    --board:#d4e6fb;
    --green:#52b548;
    --ink:#1b1b1b;
    --grey-bg:#efefef;
    --footer:#0d0d0d;
    --hero-a:#2d3f5a;
    --hero-b:#5f7896;
    --hero-c:#1d2636;
    --readmore:#b31b4a;
  }
  *{box-sizing:border-box;margin:0;padding:0}
  html,body{width:955px;height:1200px;overflow:hidden}
  body{background:var(--board);font-family:"PT Sans",Arial,sans-serif;position:relative}
  .page{position:absolute;width:772px;height:2018px;transform:scale(.557);transform-origin:0 0;overflow:hidden;background:#fff}
  .page--red{left:38px;top:48px;--accent:#b31b4a;--accent-soft:rgba(196,24,74,.88);--subscribe:#b31b4a}
  .page--blue{left:488px;top:51px;--accent:#17479a;--accent-soft:rgba(20,68,160,.88);--subscribe:var(--green)}
  .abs{position:absolute}
  .script{font-family:"Merienda",cursive}

  /* hero */
  .hero{left:0;top:0;width:772px;height:397px;overflow:hidden}
  .hero-photo{position:absolute;inset:0;background:linear-gradient(160deg,var(--hero-b) 0%,var(--hero-a) 45%,var(--hero-c) 100%)}
  .hero-shape{position:absolute;left:0;top:0}
  .logo{left:73px;top:16px;color:#fff;font-size:25px;font-weight:400}
  .nav{left:379px;top:30px;display:flex;gap:21px;color:#fff;font-size:11px}
  .hero-title{left:0;width:772px;top:126px;text-align:center;color:#fff;font-size:41px;font-weight:700}
  .hero-text{left:0;width:772px;top:187px;text-align:center;color:#fff;font-size:11px;line-height:18px}
  .btn{display:flex;align-items:center;justify-content:center;color:#fff;font-weight:700;font-size:11px;text-transform:uppercase;border-radius:2px}
  .btn--hero{left:338px;top:231px;width:96px;height:30px;background:var(--green)}
  .dots{left:734px;top:179px}

  .rule{height:3px;width:36px;background:var(--accent)}
  .h2{font-size:28px;color:var(--ink);font-weight:700}
  .body{font-size:9px;line-height:17.6px;color:var(--ink)}

  /* about */
  .about{left:0;top:397px;width:772px;height:347px;background:var(--grey-bg)}
  .about-photo{left:446px;top:46px;width:202px;height:254px;background:linear-gradient(150deg,#cfd9e2,#a9835e 55%,#3b4a5c);box-shadow:0 2px 6px rgba(0,0,0,.2)}
  .btn--accent{background:var(--accent)}

  /* services */
  .card{width:150px;height:170px;background:#f4f4f4;box-shadow:0 1px 4px rgba(0,0,0,.18);text-align:center;padding-top:20px}
  .card--active{background:var(--accent);height:195px;color:#fff}
  .card h3{font-family:"Merienda",cursive;font-size:12px;font-weight:400;margin:10px 0 12px;color:var(--ink)}
  .card--active h3{color:#fff}
  .card p{font-size:9px;line-height:15.5px;color:#333;padding:0 12px}
  .card--active p{color:#fff}
  .card svg{width:38px;height:38px}
  .arrow{width:22px;height:22px;border-radius:50%;background:var(--accent);display:flex;align-items:center;justify-content:center}
  .readmore{left:267px;top:1053px;width:74px;height:22px;background:#fff;color:var(--readmore);font-size:9px;font-weight:700;display:flex;align-items:center;justify-content:center;box-shadow:0 1px 3px rgba(0,0,0,.2)}

  /* partners */
  .partners{left:0;top:1150px;width:772px;height:240px;background:var(--accent)}
  .partner-box{width:121px;height:75px;background:#fff;display:flex;align-items:center;justify-content:center;gap:6px;font-size:17px;font-weight:700;color:#555;top:115px}
  .partner-box i{width:10px;height:10px;border-radius:50%;background:#888;display:block}
  .arrow--white{width:34px;height:34px;background:#fff}

  /* careers */
  .career-photo{left:79px;top:1438px;width:236px;height:236px;border-radius:50%;background:linear-gradient(140deg,#8a6b4f,#c8c2b8 45%,#3c3c44);border:3px solid #fff;box-shadow:2px 2px 0 3px var(--accent)}

  /* footer */
  .footer{left:0;top:1730px;width:772px;height:288px;background:var(--footer);color:#fff}
  .footer h4{font-family:"Merienda",cursive;font-size:14px;font-weight:400;position:absolute;top:40px}
  .footer .small{font-size:8px;line-height:15.6px;color:#ddd;position:absolute}
  .input{left:331px;top:110px;width:176px;height:24px;border:1.5px solid #fff;border-radius:12px;font-size:7px;padding:0 13px;display:flex;align-items:center}
  .subscribe{left:331px;top:144px;width:90px;height:22px;border-radius:11px;background:var(--subscribe);font-family:"Merienda",cursive;font-size:8px;font-weight:700;display:flex;align-items:center;justify-content:center}
  .socials{left:344px;top:230px;display:flex;gap:3px}
  .socials span{width:19px;height:19px;border:1.3px solid #fff;border-radius:50%;display:block}
  .copy{left:0;width:772px;top:260px;text-align:center;font-size:9px}
</style>
</head>
<body>

<!-- Variant: red accent -->
<section class="page page--red">
  <header class="abs hero">
    <div class="hero-photo" role="img" aria-label="Snow-covered mountain range above a calm lake"></div>
    <svg class="hero-shape" width="772" height="397"><polygon points="0,0 235,0 445,397 0,397" fill="var(--accent-soft)"/></svg>
    <div class="abs logo script">VelmaTrix</div>
    <nav class="abs nav"><span>Home</span><span>About Us</span><span>Services</span><span>Partner</span><span>Careers</span><span>Contact</span></nav>
    <h1 class="abs hero-title script">Welcome to VelmaTrix</h1>
    <p class="abs hero-text">Nemo enim ipsam voluptatem quia voluptas sit aspernatur aut odit aut<br>fugit, sed quia consequuntur magni dolores eos qui ratione</p>
    <div class="abs btn btn--hero">Read More</div>
    <svg class="abs dots" width="12" height="40"><circle cx="6" cy="6" r="5" fill="none" stroke="#fff" stroke-width="1.3"/><circle cx="6" cy="6" r="2.8" fill="#fff"/><circle cx="6" cy="22" r="2.8" fill="#fff"/><circle cx="6" cy="34" r="2.8" fill="#fff"/></svg>
  </header>

  <section class="abs about">
    <svg class="abs" style="left:0;top:0" width="772" height="347"><polygon points="622,0 772,0 772,347 470,347" fill="var(--green)"/></svg>
    <div class="abs rule" style="left:71px;top:64px"></div>
    <h2 class="abs h2 script" style="left:71px;top:70px">About Us</h2>
    <p class="abs body" style="left:71px;top:114px;width:322px">Nemo enim ipsam voluptatem quia voluptas sit aspernatur aut odit aut fugit, sed quia consequuntur magni dolores eos qui ratione voluptatem sequi nesciunt. Neque porro quisquam est, qui dolorem ipsum quia dolor sit amet, consectetur, adipisci velit, sed quia non numquam eius modi tempora incidunt ut labore et dolore magnam aliquam quaerat voluptatem. Ut enim ad minima veniam, quis nostrum exercitationem ullam corporis suscipit laboriosam, nisi ut aliquid ex ea commodi consequatur</p>
    <div class="abs btn btn--accent" style="left:71px;top:251px;width:96px;height:30px">Read More</div>
    <div class="abs about-photo" role="img" aria-label="Two smiling colleagues working at a laptop"></div>
  </section>

  <div class="abs rule" style="left:368px;top:805px"></div>
  <h2 class="abs h2 script" style="left:0;width:772px;text-align:center;top:810px">Services</h2>
  <div class="abs arrow" style="left:28px;top:966px"><svg width="10" height="10"><path d="M6.5 1.5 3 5l3.5 3.5" fill="none" stroke="#fff" stroke-width="1.5"/></svg></div>
  <div class="abs arrow" style="left:722px;top:966px"><svg width="10" height="10"><path d="M3.5 1.5 7 5 3.5 8.5" fill="none" stroke="#fff" stroke-width="1.5"/></svg></div>
  <article class="abs card" style="left:63px;top:890px"><svg viewBox="0 0 38 38"><rect x="8" y="4" width="22" height="28" fill="none" stroke="#222" stroke-width="1.4"/><circle cx="16" cy="20" r="6" fill="none" stroke="#222" stroke-width="1.4"/><path d="M16 14v6h6M22 9h5M22 12h5" stroke="#222" stroke-width="1.4" fill="none"/></svg><h3>Business Analysis</h3><p>Lorem ipsum dolor consectetur adipiscing elit. Vestib euismod mag quis eleifend.</p></article>
  <article class="abs card card--active" style="left:229px;top:880px"><svg viewBox="0 0 38 38"><circle cx="19" cy="8" r="5" fill="none" stroke="#fff" stroke-width="1.4"/><circle cx="10" cy="20" r="4" fill="none" stroke="#fff" stroke-width="1.4"/><circle cx="19" cy="20" r="4" fill="none" stroke="#fff" stroke-width="1.4"/><circle cx="28" cy="20" r="4" fill="none" stroke="#fff" stroke-width="1.4"/><path d="M4 34c0-5 3-8 6-8s6 3 6 8M13 34c0-5 3-8 6-8s6 3 6 8M22 34c0-5 3-8 6-8s6 3 6 8" fill="none" stroke="#fff" stroke-width="1.4"/></svg><h3>Outsourcing</h3><p>Neque porro quisquam est, qui dolorem ipsum quia dolor sit amet, consectetur, adipisci velit, sed quia non</p></article>
  <article class="abs card" style="left:393px;top:890px"><svg viewBox="0 0 38 38"><circle cx="12" cy="10" r="5" fill="none" stroke="#222" stroke-width="1.4"/><circle cx="24" cy="20" r="5" fill="none" stroke="#222" stroke-width="1.4"/><path d="M15 34c0-5 4-8 9-8s9 3 9 8M4 22h10M4 26h8" fill="none" stroke="#222" stroke-width="1.4"/></svg><h3>Development</h3><p>Lorem ipsum dolor consectetur adipiscing elit. Vestib euismod mag quis eleifend.</p></article>
  <article class="abs card" style="left:558px;top:890px"><svg viewBox="0 0 38 38"><rect x="12" y="4" width="22" height="16" fill="none" stroke="#222" stroke-width="1.4"/><path d="M15 16l5-5 4 3 6-6" fill="none" stroke="#222" stroke-width="1.4"/><circle cx="8" cy="16" r="3.5" fill="none" stroke="#222" stroke-width="1.4"/><path d="M3 34V24h10v10M16 34c0-3 2-5 4-5s4 2 4 5M26 34c0-3 2-5 4-5s4 2 4 5" fill="none" stroke="#222" stroke-width="1.4"/></svg><h3>Trainings</h3><p>Lorem ipsum dolor consectetur adipiscing elit. Vestib euismod mag quis eleifend.</p></article>
  <div class="abs readmore">Read More</div>

  <section class="abs partners">
    <div class="abs rule" style="left:368px;top:38px;background:#fff"></div>
    <h2 class="abs h2 script" style="left:0;width:772px;text-align:center;top:43px;color:#fff">Our Partner</h2>
    <div class="abs arrow arrow--white" style="left:16px;top:136px"><svg width="12" height="12"><path d="M8 2 4 6l4 4" fill="none" stroke="#222" stroke-width="1.6"/></svg></div>
    <div class="abs arrow arrow--white" style="left:721px;top:136px"><svg width="12" height="12"><path d="M4 2l4 4-4 4" fill="none" stroke="#222" stroke-width="1.6"/></svg></div>
    <div class="abs partner-box" style="left:68px">Norvane</div>
    <div class="abs partner-box" style="left:197px"><i></i>Keltro</div>
    <div class="abs partner-box" style="left:325px">Ombrisa</div>
    <div class="abs partner-box" style="left:453px"><i style="border-radius:0"></i>Telvio</div>
    <div class="abs partner-box" style="left:581px">Dravik</div>
  </section>

  <div class="abs career-photo" role="img" aria-label="Team meeting around a table with a presentation screen"></div>
  <div class="abs rule" style="left:350px;top:1435px"></div>
  <h2 class="abs h2 script" style="left:350px;top:1440px">Careers</h2>
  <p class="abs body" style="left:350px;top:1490px;width:348px;line-height:18.8px;text-align:justify">Nemo enim ipsam voluptatem quia voluptas sit aspernatur aut odit aut fugit, sed quia consequuntur magni dolores eos qui ratione voluptatem sequi nesciunt. Neque porro quisquam est, qui dolorem ipsum quia dolor sit amet, consectetur, adipisci velit, sed quia non numquam eius modi tempora incidunt ut labore et dolore magnam aliquam quaerat voluptatem. Ut enim ad minima veniam, quis nostrum exercitationem ullam corporis suscipit laboriosam, nisi ut aliquid ex ea commodi consequatur</p>
  <div class="abs btn btn--accent" style="left:350px;top:1616px;width:116px;height:34px">Learn More</div>

  <footer class="abs footer">
    <h4 style="left:72px">About Us</h4>
    <p class="small" style="left:72px;top:76px;width:215px">Nemo enim ipsam voluptatem quia voluptas sit aspernatur aut odit aut fugit, sed quia consequuntur magni dolores eos qui ratione voluptatem sequi nesciunt. Neque porro quisquam est, qui dolorem ipsum quia dolor sit amet, consectetur, adipisci velit, sed quia non numquam eius modi tempora incidunt ut labore et dolore magnam aliquam quaerat voluptatem.</p>
    <h4 style="left:331px">Sign Up For Newsletter</h4>
    <p class="small" style="left:331px;top:76px;width:180px;line-height:14px">excepteur sint occaecat cupidatat non proident, sunt in culpa qui officia deserunt</p>
    <div class="abs input">Enter email</div>
    <div class="abs subscribe">SUBSCRIBE</div>
    <h4 style="left:547px">Contact Us</h4>
    <svg class="abs" style="left:550px;top:80px" width="12" height="100"><path d="M6 1a4 4 0 0 0-4 4c0 3 4 8 4 8s4-5 4-8a4 4 0 0 0-4-4z" fill="#fff"/><circle cx="6" cy="5" r="1.5" fill="#000"/><path d="M2 44c1 4 5 8 9 9l1-3-3-1-1 1c-2-1-3-2-4-4l1-1-1-3z" fill="#fff"/><rect x="1" y="85" width="10" height="7" fill="#fff"/><path d="M1 85l5 4 5-4" stroke="#000" fill="none"/></svg>
    <p class="small" style="left:572px;top:76px;width:170px">24 Larchfeld Way, Suite 3<br>Oberwinden, 80312 Velden</p>
    <p class="small" style="left:572px;top:118px">Phone:<br>&nbsp;(555) 014-2290</p>
    <p class="small" style="left:572px;top:162px">Email:<br>info@VelmaTrix.com</p>
    <div class="abs socials"><span></span><span></span><span></span><span></span></div>
    <p class="abs copy">Coprights &nbsp;© 2019 VelmaTrix &nbsp;| &nbsp;All Rights Reserved</p>
  </footer>
</section>

<!-- Variant: blue accent -->
<section class="page page--blue">
  <header class="abs hero">
    <div class="hero-photo" role="img" aria-label="Snow-covered mountain range above a calm lake"></div>
    <svg class="hero-shape" width="772" height="397"><polygon points="0,0 235,0 445,397 0,397" fill="var(--accent-soft)"/></svg>
    <div class="abs logo script">VelmaTrix</div>
    <nav class="abs nav"><span>Home</span><span>About Us</span><span>Services</span><span>Partner</span><span>Careers</span><span>Contact</span></nav>
    <h1 class="abs hero-title script">Welcome to VelmaTrix</h1>
    <p class="abs hero-text">Nemo enim ipsam voluptatem quia voluptas sit aspernatur aut odit aut<br>fugit, sed quia consequuntur magni dolores eos qui ratione</p>
    <div class="abs btn btn--hero">Read More</div>
    <svg class="abs dots" width="12" height="40"><circle cx="6" cy="6" r="5" fill="none" stroke="#fff" stroke-width="1.3"/><circle cx="6" cy="6" r="2.8" fill="#fff"/><circle cx="6" cy="22" r="2.8" fill="#fff"/><circle cx="6" cy="34" r="2.8" fill="#fff"/></svg>
  </header>

  <section class="abs about">
    <svg class="abs" style="left:0;top:0" width="772" height="347"><polygon points="622,0 772,0 772,347 470,347" fill="var(--green)"/></svg>
    <div class="abs rule" style="left:71px;top:64px"></div>
    <h2 class="abs h2 script" style="left:71px;top:70px">About Us</h2>
    <p class="abs body" style="left:71px;top:114px;width:322px">Nemo enim ipsam voluptatem quia voluptas sit aspernatur aut odit aut fugit, sed quia consequuntur magni dolores eos qui ratione voluptatem sequi nesciunt. Neque porro quisquam est, qui dolorem ipsum quia dolor sit amet, consectetur, adipisci velit, sed quia non numquam eius modi tempora incidunt ut labore et dolore magnam aliquam quaerat voluptatem. Ut enim ad minima veniam, quis nostrum exercitationem ullam corporis suscipit laboriosam, nisi ut aliquid ex ea commodi consequatur</p>
    <div class="abs btn btn--accent" style="left:71px;top:255px;width:96px;height:30px">Read More</div>
    <div class="abs about-photo" role="img" aria-label="Two smiling colleagues working at a laptop"></div>
  </section>

  <div class="abs rule" style="left:368px;top:805px"></div>
  <h2 class="abs h2 script" style="left:0;width:772px;text-align:center;top:810px">Services</h2>
  <div class="abs arrow" style="left:28px;top:966px"><svg width="10" height="10"><path d="M6.5 1.5 3 5l3.5 3.5" fill="none" stroke="#fff" stroke-width="1.5"/></svg></div>
  <div class="abs arrow" style="left:722px;top:966px"><svg width="10" height="10"><path d="M3.5 1.5 7 5 3.5 8.5" fill="none" stroke="#fff" stroke-width="1.5"/></svg></div>
  <article class="abs card" style="left:63px;top:890px"><svg viewBox="0 0 38 38"><rect x="8" y="4" width="22" height="28" fill="none" stroke="#222" stroke-width="1.4"/><circle cx="16" cy="20" r="6" fill="none" stroke="#222" stroke-width="1.4"/><path d="M16 14v6h6M22 9h5M22 12h5" stroke="#222" stroke-width="1.4" fill="none"/></svg><h3>Business Analysis</h3><p>Lorem ipsum dolor consectetur adipiscing elit. Vestib euismod mag quis eleifend.</p></article>
  <article class="abs card card--active" style="left:229px;top:880px"><svg viewBox="0 0 38 38"><circle cx="19" cy="8" r="5" fill="none" stroke="#fff" stroke-width="1.4"/><circle cx="10" cy="20" r="4" fill="none" stroke="#fff" stroke-width="1.4"/><circle cx="19" cy="20" r="4" fill="none" stroke="#fff" stroke-width="1.4"/><circle cx="28" cy="20" r="4" fill="none" stroke="#fff" stroke-width="1.4"/><path d="M4 34c0-5 3-8 6-8s6 3 6 8M13 34c0-5 3-8 6-8s6 3 6 8M22 34c0-5 3-8 6-8s6 3 6 8" fill="none" stroke="#fff" stroke-width="1.4"/></svg><h3>Outsourcing</h3><p>Neque porro quisquam est, qui dolorem ipsum quia dolor sit amet, consectetur, adipisci velit, sed quia non</p></article>
  <article class="abs card" style="left:393px;top:890px"><svg viewBox="0 0 38 38"><circle cx="12" cy="10" r="5" fill="none" stroke="#222" stroke-width="1.4"/><circle cx="24" cy="20" r="5" fill="none" stroke="#222" stroke-width="1.4"/><path d="M15 34c0-5 4-8 9-8s9 3 9 8M4 22h10M4 26h8" fill="none" stroke="#222" stroke-width="1.4"/></svg><h3>Development</h3><p>Lorem ipsum dolor consectetur adipiscing elit. Vestib euismod mag quis eleifend.</p></article>
  <article class="abs card" style="left:558px;top:890px"><svg viewBox="0 0 38 38"><rect x="12" y="4" width="22" height="16" fill="none" stroke="#222" stroke-width="1.4"/><path d="M15 16l5-5 4 3 6-6" fill="none" stroke="#222" stroke-width="1.4"/><circle cx="8" cy="16" r="3.5" fill="none" stroke="#222" stroke-width="1.4"/><path d="M3 34V24h10v10M16 34c0-3 2-5 4-5s4 2 4 5M26 34c0-3 2-5 4-5s4 2 4 5" fill="none" stroke="#222" stroke-width="1.4"/></svg><h3>Trainings</h3><p>Lorem ipsum dolor consectetur adipiscing elit. Vestib euismod mag quis eleifend.</p></article>
  <div class="abs readmore">Read More</div>

  <section class="abs partners">
    <div class="abs rule" style="left:368px;top:38px;background:#fff"></div>
    <h2 class="abs h2 script" style="left:0;width:772px;text-align:center;top:43px;color:#fff">Our Partner</h2>
    <div class="abs arrow arrow--white" style="left:16px;top:136px"><svg width="12" height="12"><path d="M8 2 4 6l4 4" fill="none" stroke="#222" stroke-width="1.6"/></svg></div>
    <div class="abs arrow arrow--white" style="left:721px;top:136px"><svg width="12" height="12"><path d="M4 2l4 4-4 4" fill="none" stroke="#222" stroke-width="1.6"/></svg></div>
    <div class="abs partner-box" style="left:68px">Norvane</div>
    <div class="abs partner-box" style="left:197px"><i></i>Keltro</div>
    <div class="abs partner-box" style="left:325px">Ombrisa</div>
    <div class="abs partner-box" style="left:453px"><i style="border-radius:0"></i>Telvio</div>
    <div class="abs partner-box" style="left:581px">Dravik</div>
  </section>

  <div class="abs career-photo" role="img" aria-label="Team meeting around a table with a presentation screen"></div>
  <div class="abs rule" style="left:350px;top:1435px"></div>
  <h2 class="abs h2 script" style="left:350px;top:1440px">Careers</h2>
  <p class="abs body" style="left:350px;top:1490px;width:348px;line-height:18.8px;text-align:justify">Nemo enim ipsam voluptatem quia voluptas sit aspernatur aut odit aut fugit, sed quia consequuntur magni dolores eos qui ratione voluptatem sequi nesciunt. Neque porro quisquam est, qui dolorem ipsum quia dolor sit amet, consectetur, adipisci velit, sed quia non numquam eius modi tempora incidunt ut labore et dolore magnam aliquam quaerat voluptatem. Ut enim ad minima veniam, quis nostrum exercitationem ullam corporis suscipit laboriosam, nisi ut aliquid ex ea commodi consequatur</p>
  <div class="abs btn btn--accent" style="left:350px;top:1616px;width:116px;height:34px">Learn More</div>

  <footer class="abs footer">
    <h4 style="left:72px">About Us</h4>
    <p class="small" style="left:72px;top:76px;width:215px">Nemo enim ipsam voluptatem quia voluptas sit aspernatur aut odit aut fugit, sed quia consequuntur magni dolores eos qui ratione voluptatem sequi nesciunt. Neque porro quisquam est, qui dolorem ipsum quia dolor sit amet, consectetur, adipisci velit, sed quia non numquam eius modi tempora incidunt ut labore et dolore magnam aliquam quaerat voluptatem.</p>
    <h4 style="left:331px">Sign Up For Newsletter</h4>
    <p class="small" style="left:331px;top:76px;width:180px;line-height:14px">excepteur sint occaecat cupidatat non proident, sunt in culpa qui officia deserunt</p>
    <div class="abs input">Enter email</div>
    <div class="abs subscribe">SUBSCRIBE</div>
    <h4 style="left:547px">Contact Us</h4>
    <svg class="abs" style="left:550px;top:80px" width="12" height="100"><path d="M6 1a4 4 0 0 0-4 4c0 3 4 8 4 8s4-5 4-8a4 4 0 0 0-4-4z" fill="#fff"/><circle cx="6" cy="5" r="1.5" fill="#000"/><path d="M2 44c1 4 5 8 9 9l1-3-3-1-1 1c-2-1-3-2-4-4l1-1-1-3z" fill="#fff"/><rect x="1" y="85" width="10" height="7" fill="#fff"/><path d="M1 85l5 4 5-4" stroke="#000" fill="none"/></svg>
    <p class="small" style="left:572px;top:76px;width:170px">24 Larchfeld Way, Suite 3<br>Oberwinden, 80312 Velden</p>
    <p class="small" style="left:572px;top:118px">Phone:<br>&nbsp;(555) 014-2290</p>
    <p class="small" style="left:572px;top:162px">Email:<br>info@VelmaTrix.com</p>
    <div class="abs socials"><span></span><span></span><span></span><span></span></div>
    <p class="abs copy">Coprights &nbsp;© 2019 VelmaTrix &nbsp;| &nbsp;All Rights Reserved</p>
  </footer>
</section>

</body>
</html>
```